Vantor Wear and Fuel is looking for a Clothing/Supplement Online Store Website!

Must be convenient, and user friendly, with vibrant colors that catch the eye!

Target Market(s)

Athletes, and Fashion Customers

Industry/Entity Type

Fitness

Coding

Coded - Design and coding required

Number of Pages Required

3 page

Font styles to use
Decorative

Colors

Designer to choose colors to be used in the design.

Requirements
Must have
• Somewhere to feature products, features to promote discounts and make announcements.
Nice to have
• My logos on each page

```html
<!DOCTYPE html>
<html lang="en">
<head>
<meta charset="utf-8">
<title>Kestrum — Home</title>
<link rel="stylesheet" href="https://fonts.googleapis.com/css2?family=Poppins:wght@400;500;600;700&family=Roboto:wght@500;700&display=swap">
<style>
:root{
  --orange:#f7941d;
  --blue:#1e7ee6;
  --footer-blue:#0d7be9;
  --ink:#2b2b2b;
  --text:#4a4a4a;
  --muted:#8a8a8a;
  --line:#dbe5f3;
  --hero-red:#ef3340;
  --hero-red-soft:#f24a54;
  --charcoal:#555a60;
  --white:#ffffff;
}
*{box-sizing:border-box;margin:0;padding:0}
html,body{width:1200px;height:3934px;overflow:hidden}
body{position:relative;background:var(--white);font-family:"Poppins",sans-serif;color:var(--text)}
a{text-decoration:none;color:inherit}

/* header */
.site-header{position:absolute;top:0;left:0;width:1200px;height:84px;background:var(--white)}
.brand{position:absolute;left:142px;top:20px;display:flex;align-items:center;gap:12px}
.brand-dot{width:42px;height:42px;border-radius:50%;background:var(--charcoal)}
.brand-name{font-family:"Poppins",sans-serif;font-weight:700;font-size:32px;letter-spacing:1px;color:var(--ink)}
.main-nav{position:absolute;top:36px;left:591px}
.main-nav a{position:absolute;font-size:12.5px;color:#777;white-space:nowrap;letter-spacing:.3px}
.main-nav a.active{color:var(--orange)}
.main-nav a.active::after{content:"";position:absolute;left:0;right:0;bottom:-5px;height:2px;background:var(--orange)}
.search-btn{position:absolute;left:1034px;top:31px;width:24px;height:24px;border-radius:50%;background:var(--orange)}

/* hero */
.hero{position:absolute;top:84px;left:0;width:1200px;height:432px;background:linear-gradient(90deg,var(--hero-red-soft) 0 50%,var(--hero-red) 50% 100%);overflow:hidden}
.hero-photo{position:absolute;top:0;height:432px}
.hero-photo.left{left:150px;width:320px;background:radial-gradient(ellipse at 50% 40%,rgba(230,220,215,.55),rgba(120,90,80,.25) 55%,transparent 75%)}
.hero-photo.right{left:780px;width:330px;background:radial-gradient(ellipse at 50% 45%,rgba(235,230,228,.6),rgba(110,85,75,.25) 55%,transparent 75%)}
.hero-copy{position:absolute;left:0;width:1200px;top:0;text-align:center;color:var(--white)}
.hero-kicker{position:absolute;top:102px;width:100%;font-size:16px;letter-spacing:7px;font-weight:500}
.hero-title{position:absolute;top:146px;width:100%;font-size:40px;font-weight:600;line-height:46px;letter-spacing:1px}
.hero-note{position:absolute;top:238px;width:100%;font-size:7.5px;letter-spacing:1px}
.hero-btn{position:absolute;top:270px;left:504px;width:194px;height:38px;background:#111;color:var(--white);font-size:14px;font-weight:600;line-height:38px;letter-spacing:.5px}

/* section headings */
.section-title{position:absolute;left:0;width:1200px;text-align:center;font-family:"Roboto",sans-serif;font-weight:700;font-size:34px;letter-spacing:.5px}
.section-title .warm{color:var(--orange)}
.section-title .cool{color:var(--blue)}
.divider{position:absolute;left:528px;width:144px;height:14px}
.divider::before,.divider::after{content:"";position:absolute;top:7px;width:52px;height:1px;background:#888}
.divider::before{left:0}.divider::after{right:0}
.divider span{position:absolute;left:65px;top:0;width:14px;height:14px;border-radius:50%;background:var(--charcoal)}

.sort-select{position:absolute;left:458px;width:284px;height:35px;border:1px solid #ddd;border-radius:18px;font-size:12px;color:#777;line-height:33px;padding-left:17px}
.sort-select svg{position:absolute;right:22px;top:13px}
.result-count{position:absolute;left:0;width:1200px;text-align:center;font-size:11px;color:#555}

/* carousels */
.carousel-arrow{position:absolute;width:32px;height:32px;border-radius:50%}
.carousel-arrow.prev{left:65px;border:1.5px solid #333;background:var(--white)}
.carousel-arrow.next{left:1100px;background:var(--orange)}
.carousel-arrow svg{position:absolute;left:0;top:0}

.product-grid{position:absolute;left:140px;display:grid;grid-template-columns:repeat(4,212px);column-gap:23px;row-gap:31px}
.product-card{position:relative;width:212px;height:337px;border:1px solid var(--line);background:var(--white)}
.product-media{height:211px;background:radial-gradient(ellipse at 50% 50%,var(--tone,#3a3a3a) 0 28%,#f3f4f6 60%,#fff 80%)}
.product-info{height:88px;text-align:center;padding-top:10px}
.product-card.highlight .product-info{background:var(--blue)}
.product-name{font-size:15.5px;font-weight:600;color:var(--blue);line-height:22px}
.product-text{font-size:12.5px;line-height:19px;color:#444;margin-top:2px}
.product-card.highlight .product-name,.product-card.highlight .product-text{color:var(--white)}
.btn-details{position:absolute;left:-1px;right:-1px;bottom:-1px;height:38px;background:var(--orange);color:var(--white);font-size:13px;font-weight:600;letter-spacing:1px;line-height:38px;text-align:center}
.badge{position:absolute;border-radius:50%;background:var(--orange);color:var(--white);font-weight:600;text-align:center;display:flex;align-items:center;justify-content:center;border:3px solid var(--white);box-shadow:0 0 0 1px var(--orange)}
.badge.sale{right:8px;top:11px;width:46px;height:46px;font-size:11px}
.badge.new{left:73px;top:72px;width:66px;height:66px;font-size:10px;line-height:13px}

/* categories */
.category{position:absolute;top:2222px;height:346px;overflow:hidden}
.category .cat-media{position:absolute;inset:0}
.category h3{position:absolute;bottom:24px;left:0;right:0;text-align:center;font-family:"Roboto",sans-serif;font-weight:700;font-size:21px;color:var(--orange);letter-spacing:.5px}

/* blog */
.blog-card{position:absolute;top:2730px;width:290px;height:336px}
.blog-media{position:absolute;left:0;top:0;width:290px;height:229px}
.blog-body{position:absolute;left:12px;top:194px;width:266px;height:142px;background:var(--white);box-shadow:0 2px 10px rgba(0,0,0,.08);text-align:center}
.blog-date{margin-top:13px;font-size:11.5px;color:var(--orange)}
.blog-date svg{vertical-align:-1px;margin-right:5px}
.blog-excerpt{margin-top:6px;font-size:14px;line-height:22px;color:#444}
.read-more{display:inline-block;margin-top:10px;font-size:12.5px;font-weight:600;color:var(--blue)}

/* contact form */
.contact-intro{position:absolute;top:3224px;left:0;width:1200px;text-align:center;font-size:12.5px;line-height:22px;color:#333}
.field{position:absolute;border:1px solid #ddd;font-size:11.5px;color:#888;padding:0 21px;line-height:34px;background:var(--white)}
.field.area{line-height:20px;padding-top:8px}
.btn-submit{position:absolute;left:551px;top:3517px;width:98px;height:34px;border-radius:17px;background:var(--orange);color:var(--white);font-size:13px;font-weight:600;letter-spacing:1px;text-align:center;line-height:34px}

/* footer */
.site-footer{position:absolute;top:3602px;left:0;width:1200px;height:332px;background:var(--footer-blue);color:var(--white)}
.footer-heading{position:absolute;top:60px;font-size:14px;font-weight:600;letter-spacing:1px}
.footer-links{position:absolute;left:142px;top:97px;list-style:none}
.footer-links li{font-size:12px;height:24.5px}
.footer-links li::before{content:"›";margin-right:6px}
.contact-item{position:absolute;left:301px;display:flex;align-items:flex-start;gap:16px;font-size:12px;line-height:17px}
.contact-icon{flex:none;width:28px;height:28px;border-radius:50%;border:1.5px solid var(--white);display:flex;align-items:center;justify-content:center}
.contact-item strong{font-weight:600}
.footer-map{position:absolute;left:589px;top:99px;width:254px;height:144px;border:3px solid var(--white);background:linear-gradient(135deg,#e9ece6,#d9e4d6 45%,#eef0ea)}
.footer-brand{position:absolute;left:894px;top:128px;width:174px;text-align:center}
.footer-brand .brand-dot{width:36px;height:36px;margin:0 auto 8px;background:var(--white)}
.footer-brand .brand-name{font-size:26px;color:var(--white)}
.social{position:absolute;top:200px;left:924px;display:flex;gap:8px}
.social span{width:30px;height:30px;border-radius:50%;border:1.5px solid var(--white)}
.footer-rule{position:absolute;left:142px;right:142px;top:277px;height:1px;background:rgba(255,255,255,.35)}
.copyright{position:absolute;top:300px;left:0;width:1200px;text-align:center;font-size:12px}
</style>
</head>
<body>

<header class="site-header">
  <a class="brand" href="#"><span class="brand-dot"></span><span class="brand-name">KESTRUM</span></a>
  <nav class="main-nav">
    <a class="active" href="#" style="left:0">HOME</a>
    <a href="#" style="left:67px">ABOUT US</a>
    <a href="#" style="left:166px">PRODUCTS</a>
    <a href="#" style="left:269px">BLOG</a>
    <a href="#" style="left:336px">CONTACT US</a>
  </nav>
  <span class="search-btn" aria-label="Search">
    <svg width="24" height="24" viewBox="0 0 24 24"><circle cx="11" cy="11" r="4" fill="none" stroke="#fff" stroke-width="1.8"/><line x1="14" y1="14" x2="17" y2="17" stroke="#fff" stroke-width="1.8" stroke-linecap="round"/></svg>
  </span>
</header>

<section class="hero">
  <div class="hero-photo left" role="img" aria-label="Model in a checked off-shoulder top and denim shorts seated on a wooden stool"></div>
  <div class="hero-photo right" role="img" aria-label="Model in a checked wrap top seated, leaning forward"></div>
  <div class="hero-copy">
    <p class="hero-kicker">BOUTIQUE CULTURE SALE</p>
    <h1 class="hero-title">30% OFF<br>PREMIUM STYLES</h1>
    <p class="hero-note">*EXCLUDES PREVIOUS MARKDOWNS AND STYLE STEALS</p>
    <a class="hero-btn" href="#">VISIT OUR STORE</a>
  </div>
</section>

<!-- featured products -->
<h2 class="section-title" style="top:591px"><span class="warm">FEATURED</span> <span class="cool">PRODUCTS</span></h2>
<div class="divider" style="top:637px"><span></span></div>
<div class="sort-select" style="top:684px">Default sorting<svg width="10" height="7" viewBox="0 0 10 7"><path d="M1 1l4 4 4-4" fill="none" stroke="#555" stroke-width="1.3"/></svg></div>
<p class="result-count" style="top:729px">Showing all 7 results</p>

<a class="carousel-arrow prev" href="#" style="top:925px" aria-label="Previous"><svg width="29" height="29" viewBox="0 0 29 29"><path d="M16 10l-4.5 4.5L16 19" fill="none" stroke="#333" stroke-width="1.6"/></svg></a>
<a class="carousel-arrow next" href="#" style="top:925px" aria-label="Next"><svg width="32" height="32" viewBox="0 0 32 32"><path d="M14 11l5 5-5 5" fill="none" stroke="#fff" stroke-width="1.8"/></svg></a>

<div class="product-grid" style="top:771px">
  <article class="product-card highlight">
    <div class="product-media" role="img" aria-label="Black creatine supplement tub" style="--tone:#2c2c2c"></div>
    <div class="product-info"><h3 class="product-name">Product 1</h3><p class="product-text">Lorem ipsum dolor sit amet,<br>consectetuer adipiscing</p></div>
    <a class="btn-details" href="#">VIEW DETAILS</a>
  </article>
  <article class="product-card">
    <div class="product-media" role="img" aria-label="Purple and black supplement tub" style="--tone:#6a2a5e"></div>
    <div class="product-info"><h3 class="product-name">Product 2</h3><p class="product-text">Lorem ipsum dolor sit amet,<br>consectetuer adipiscing</p></div>
    <a class="btn-details" href="#">VIEW DETAILS</a>
  </article>
  <article class="product-card">
    <div class="product-media" role="img" aria-label="Woman in a black and white striped blazer" style="--tone:#8d8a86"></div>
    <div class="product-info"><h3 class="product-name">Product 3</h3><p class="product-text">Lorem ipsum dolor sit amet,<br>consectetuer adipiscing</p></div>
    <a class="btn-details" href="#">VIEW DETAILS</a>
  </article>
  <article class="product-card">
    <div class="product-media" role="img" aria-label="Grey athletic t-shirt" style="--tone:#5b5e60"></div>
    <div class="product-info"><h3 class="product-name">Product 4</h3><p class="product-text">Lorem ipsum dolor sit amet,<br>consectetuer adipiscing</p></div>
    <a class="btn-details" href="#">VIEW DETAILS</a>
  </article>
  <article class="product-card">
    <div class="product-media" role="img" aria-label="Red swing dress with black belt" style="--tone:#d42a2a"></div>
    <div class="product-info"><h3 class="product-name">Product 5</h3><p class="product-text">Lorem ipsum dolor sit amet,<br>consectetuer adipiscing</p></div>
    <a class="btn-details" href="#">VIEW DETAILS</a>
  </article>
  <article class="product-card">
    <div class="product-media" role="img" aria-label="Blue skinny jeans with red heels" style="--tone:#3d587c"></div>
    <div class="product-info"><h3 class="product-name">Product 6</h3><p class="product-text">Lorem ipsum dolor sit amet,<br>consectetuer adipiscing</p></div>
    <a class="btn-details" href="#">VIEW DETAILS</a>
  </article>
  <article class="product-card">
    <div class="product-media" role="img" aria-label="Black long-sleeve graphic sweatshirt" style="--tone:#1f1f24"></div>
    <div class="product-info"><h3 class="product-name">Product 7</h3><p class="product-text">Lorem ipsum dolor sit amet,<br>consectetuer adipiscing</p></div>
    <a class="btn-details" href="#">VIEW DETAILS</a>
  </article>
  <article class="product-card">
    <div class="product-media" role="img" aria-label="Dark grey supplement tub" style="--tone:#3a3b3f"></div>
    <div class="product-info"><h3 class="product-name">Product 8</h3><p class="product-text">Lorem ipsum dolor sit amet,<br>consectetuer adipiscing</p></div>
    <a class="btn-details" href="#">VIEW DETAILS</a>
  </article>
</div>

<!-- most popular -->
<h2 class="section-title" style="top:1537px"><span class="warm">MOST</span> <span class="cool">POPULAR</span></h2>
<div class="divider" style="top:1583px"><span></span></div>
<div class="sort-select" style="top:1629px">Default sorting<svg width="10" height="7" viewBox="0 0 10 7"><path d="M1 1l4 4 4-4" fill="none" stroke="#555" stroke-width="1.3"/></svg></div>
<p class="result-count" style="top:1675px">Showing all 7 results</p>

<a class="carousel-arrow prev" href="#" style="top:1871px" aria-label="Previous"><svg width="29" height="29" viewBox="0 0 29 29"><path d="M16 10l-4.5 4.5L16 19" fill="none" stroke="#333" stroke-width="1.6"/></svg></a>
<a class="carousel-arrow next" href="#" style="top:1871px" aria-label="Next"><svg width="32" height="32" viewBox="0 0 32 32"><path d="M14 11l5 5-5 5" fill="none" stroke="#fff" stroke-width="1.8"/></svg></a>

<div class="product-grid" style="top:1716px">
  <article class="product-card highlight">
    <div class="product-media" role="img" aria-label="Black creatine powder tub" style="--tone:#222"></div>
    <span class="badge sale">SALE</span>
    <div class="product-info"><h3 class="product-name">Product 1</h3><p class="product-text">Lorem ipsum dolor sit amet,<br>consectetuer adipiscing</p></div>
    <a class="btn-details" href="#">VIEW DETAILS</a>
  </article>
  <article class="product-card">
    <div class="product-media" role="img" aria-label="Red ruffled blouse with jeans" style="--tone:#c8283a"></div>
    <div class="product-info"><h3 class="product-name">Product 2</h3><p class="product-text">Lorem ipsum dolor sit amet,<br>consectetuer adipiscing</p></div>
    <a class="btn-details" href="#">VIEW DETAILS</a>
  </article>
  <article class="product-card">
    <div class="product-media" role="img" aria-label="Man in a black bomber jacket" style="--tone:#25252a"></div>
    <span class="badge new">NEW<br>ARRIVAL</span>
    <div class="product-info"><h3 class="product-name">Product 3</h3><p class="product-text">Lorem ipsum dolor sit amet,<br>consectetuer adipiscing</p></div>
    <a class="btn-details" href="#">VIEW DETAILS</a>
  </article>
  <article class="product-card">
    <div class="product-media" role="img" aria-label="Yellow and blue capsule supplement bottle" style="--tone:#e8d21c"></div>
    <div class="product-info"><h3 class="product-name">Product 4</h3><p class="product-text">Lorem ipsum dolor sit amet,<br>consectetuer adipiscing</p></div>
    <a class="btn-details" href="#">VIEW DETAILS</a>
  </article>
</div>

<!-- categories -->
<h2 class="section-title" style="top:2132px"><span class="warm">PRODUCT</span> <span class="cool">CATEGORIES</span></h2>
<div class="divider" style="top:2177px"><span></span></div>

<a class="category" href="#" style="left:0;width:240px">
  <div class="cat-media" role="img" aria-label="Shopper browsing women's clothing on a rack" style="background:linear-gradient(120deg,#d9dde0,#c9b956 45%,#3a5a7a 80%)"></div>
  <h3>WOMEN</h3>
</a>
<a class="category" href="#" style="left:249px;width:347px">
  <div class="cat-media" role="img" aria-label="Man in sunglasses wearing a grey shirt" style="background:linear-gradient(120deg,#4a4f55,#8a8f94 45%,#e4e6e8 60%,#6c7075)"></div>
  <h3>MEN</h3>
</a>
<a class="category" href="#" style="left:606px;width:347px">
  <div class="cat-media" role="img" aria-label="Woman lifting a dumbbell in a gym" style="background:linear-gradient(120deg,#b9c3cc,#8c7a6c 45%,#5a5f66 75%,#aab4bd)"></div>
  <h3>FITNESS</h3>
</a>
<a class="category" href="#" style="left:962px;width:238px">
  <div class="cat-media" role="img" aria-label="Muscular man drinking from a shaker bottle" style="background:linear-gradient(120deg,#3d3f44,#8a6550 45%,#2d2f34)"></div>
  <h3>SUPPLEMENT</h3>
</a>

<!-- blog -->
<h2 class="section-title" style="top:2645px"><span class="warm">LATEST</span> <span class="cool">BLOG POSTS</span></h2>
<div class="divider" style="top:2691px"><span></span></div>

<article class="blog-card" style="left:142px">
  <div class="blog-media" role="img" aria-label="Woman in an orange dress on the phone outdoors" style="background:linear-gradient(160deg,#bcd6ea,#e0a040 60%,#9fb4c6)"></div>
  <div class="blog-body">
    <p class="blog-date"><svg width="10" height="10" viewBox="0 0 10 10"><rect x="1" y="2" width="8" height="7" fill="none" stroke="#f7941d"/><line x1="1" y1="4" x2="9" y2="4" stroke="#f7941d"/></svg>08 Sep 2019</p>
    <p class="blog-excerpt">Lorem ipsum dolor sit amet,<br>consectetuer adipiscing.</p>
    <a class="read-more" href="#">Read More →</a>
  </div>
</article>
<article class="blog-card" style="left:455px">
  <div class="blog-media" role="img" aria-label="Group training with kettlebells in a gym" style="background:linear-gradient(160deg,#6d7078,#3c3e44 55%,#8a8c90)"></div>
  <div class="blog-body">
    <p class="blog-date"><svg width="10" height="10" viewBox="0 0 10 10"><rect x="1" y="2" width="8" height="7" fill="none" stroke="#f7941d"/><line x1="1" y1="4" x2="9" y2="4" stroke="#f7941d"/></svg>08 Sep 2019</p>
    <p class="blog-excerpt">Lorem ipsum dolor sit amet,<br>consectetuer adipiscing.</p>
    <a class="read-more" href="#">Read More →</a>
  </div>
</article>
<article class="blog-card" style="left:770px">
  <div class="blog-media" role="img" aria-label="Woman in a wide-brimmed black hat in the city" style="background:linear-gradient(160deg,#d9dce0,#5a5660 55%,#c4c0bc)"></div>
  <div class="blog-body">
    <p class="blog-date"><svg width="10" height="10" viewBox="0 0 10 10"><rect x="1" y="2" width="8" height="7" fill="none" stroke="#f7941d"/><line x1="1" y1="4" x2="9" y2="4" stroke="#f7941d"/></svg>08 Sep 2019</p>
    <p class="blog-excerpt">Lorem ipsum dolor sit amet,<br>consectetuer adipiscing.</p>
    <a class="read-more" href="#">Read More →</a>
  </div>
</article>

<!-- quick contact -->
<h2 class="section-title" style="top:3144px"><span class="warm">QUICK</span> <span class="cool">CONTACT</span></h2>
<div class="divider" style="top:3190px"><span></span></div>
<p class="contact-intro">We love our customers and welcome your feedback and suggestions. Use our Contact Us page to<br>tell us what we're doing right, what we can improve on, or what you would like to see from our products!</p>

<form>
  <div class="field" style="left:302px;top:3295px;width:289px;height:36px">First Name</div>
  <div class="field" style="left:609px;top:3295px;width:289px;height:36px">Last Name</div>
  <div class="field" style="left:302px;top:3347px;width:289px;height:36px">Email</div>
  <div class="field" style="left:609px;top:3347px;width:289px;height:36px">Phone</div>
  <div class="field area" style="left:302px;top:3404px;width:596px;height:85px">Message</div>
  <a class="btn-submit" href="#">SUBMIT</a>
</form>

<footer class="site-footer">
  <h4 class="footer-heading" style="left:142px">QUICK LINKS</h4>
  <ul class="footer-links">
    <li>Home</li><li>About Us</li><li>Products</li><li>Blog</li><li>Contact Us</li>
  </ul>

  <h4 class="footer-heading" style="left:301px">CONTACT DETAILS</h4>
  <div class="contact-item" style="top:102px">
    <span class="contact-icon"><svg width="12" height="14" viewBox="0 0 12 14"><path d="M6 13s-4.5-5-4.5-7.8a4.5 4.5 0 019 0C10.5 8 6 13 6 13z" fill="#fff"/><circle cx="6" cy="5.2" r="1.6" fill="#0d7be9"/></svg></span>
    <p><strong>KESTRUM</strong><br>48 Harbor Lane, Millfield District,<br>Eastport - 20417</p>
  </div>
  <div class="contact-item" style="top:166px">
    <span class="contact-icon"><svg width="12" height="12" viewBox="0 0 12 12"><path d="M2.5 1l2 2.2-1 1.3a6.5 6.5 0 004 4l1.3-1 2.2 2-1.2 1.5C5 10.5 1.5 7 1 2.2z" fill="#fff"/></svg></span>
    <p style="margin-top:5px">555-014-2290</p>
  </div>
  <div class="contact-item" style="top:212px">
    <span class="contact-icon"><svg width="13" height="10" viewBox="0 0 13 10"><rect x="0.5" y="0.5" width="12" height="9" fill="#fff"/><path d="M0.5 0.5l6 5 6-5" fill="none" stroke="#0d7be9"/></svg></span>
    <p style="margin-top:5px">hello@kestrumwear.com</p>
  </div>

  <h4 class="footer-heading" style="left:589px">LOCATION MAP</h4>
  <div class="footer-map" role="img" aria-label="Street map of the store location with a red pin"></div>

  <div class="footer-brand">
    <div class="brand-dot"></div>
    <span class="brand-name">KESTRUM</span>
  </div>
  <div class="social" aria-label="Social links"><span></span><span></span><span></span></div>

  <div class="footer-rule"></div>
  <p class="copyright">Copyright © 2019 Kestrum. All Right Reserved.</p>
</footer>

</body>
</html>
```